Business Card for a Dental Office

The design should communicate integrity, quality and reliability. We also want the card look elegant, simple, but still stand out, different from the traditional-dental-office business card.

Industry/Entity Type

Business

```html
<!DOCTYPE html>
<html lang="en">
<head>
<meta charset="utf-8">
<title>Harlow Dental Centre – Business Card</title>
<link rel="stylesheet" href="https://fonts.googleapis.com/css2?family=Oswald:wght@400;500;700&family=Open+Sans:wght@400;600&display=swap">
<style>
  :root {
    --bg: #e9e5dc;
    --gold-light: #b3924a;
    --gold-dark: #836428;
    --lime: #c8c925;
    --lime-text: #cfcb2e;
    --black: #0c0c0c;
    --white: #ffffff;
  }
  * { margin: 0; padding: 0; box-sizing: border-box; }
  html, body { width: 1200px; height: 1022px; overflow: hidden; background: var(--bg); }
  .card {
    position: absolute; left: 100px; top: 225px;
    width: 1000px; height: 572px; border-radius: 26px; overflow: hidden;
    background: linear-gradient(160deg, var(--gold-light) 0%, #9c7c38 45%, var(--gold-dark) 100%);
    box-shadow: 0 10px 30px rgba(0,0,0,.18);
  }
  .card__shapes { position: absolute; inset: 0; }
  .brand { position: absolute; left: 48px; top: 52px; width: 730px; }
  .brand__name {
    font-family: "Oswald", sans-serif; font-weight: 700; font-size: 68px;
    line-height: 1; color: var(--white); letter-spacing: 1px; text-transform: uppercase;
    white-space: nowrap;
  }
  .brand__tagline {
    font-family: "Oswald", sans-serif; font-weight: 400; font-size: 32px;
    line-height: 1.1; margin-top: 10px; color: var(--lime-text); letter-spacing: 3px; text-transform: uppercase;
    white-space: nowrap;
  }
  .person__marker { position: absolute; left: 0; top: 322px; width: 58px; height: 40px; background: var(--lime); }
  .person { position: absolute; left: 84px; top: 300px; }
  .person__name {
    font-family: "Oswald", sans-serif; font-weight: 500; font-size: 38px; color: var(--white);
    text-transform: uppercase; letter-spacing: 1px; line-height: 1.1;
  }
  .person__role {
    font-family: "Open Sans", sans-serif; font-size: 20px; color: var(--lime-text);
    text-transform: uppercase; letter-spacing: 1px;
  }
  .contact { position: absolute; left: 84px; top: 462px; list-style: none; }
  .contact__item {
    display: flex; align-items: center; gap: 14px; height: 30px;
    font-family: "Open Sans", sans-serif; font-size: 21px; color: var(--lime-text);
  }
  .contact__icon { width: 18px; height: 18px; flex: none; }
  .mark { position: absolute; left: 858px; top: 78px; width: 120px; text-align: center; }
  .mark__square { width: 60px; height: 60px; margin: 0 auto 10px; background: var(--lime); }
  .mark__name {
    font-family: "Oswald", sans-serif; font-weight: 700; font-size: 22px;
    color: var(--white); letter-spacing: 2px;
  }
</style>
</head>
<body>
  <div class="card">
    <svg class="card__shapes" width="1000" height="572" viewBox="0 0 1000 572" aria-hidden="true">
      <path d="M0 432 H720 L776 376 V210 H1000 V572 H0 Z" fill="var(--white)"/>
      <path d="M0 446 H728 L790 384 V222 H1000 V572 H0 Z" fill="var(--black)"/>
      <path d="M800 150 L848 52 H1000 V246 H848 Z" fill="var(--black)"/>
      <path d="M812 150 L856 62 H986 V238 H856 Z" fill="none" stroke="var(--white)" stroke-width="12" stroke-linejoin="miter"/>
    </svg>

    <div class="brand">
      <h1 class="brand__name">Harlow Dental Centre</h1>
      <p class="brand__tagline">Your smile is your gift to others</p>
    </div>

    <div class="person__marker"></div>
    <div class="person">
      <p class="person__name">Mara Ellison</p>
      <p class="person__role">Director</p>
    </div>

    <ul class="contact">
      <li class="contact__item">
        <svg class="contact__icon" viewBox="0 0 24 24"><path d="M6.6 10.8a15 15 0 0 0 6.6 6.6l2.2-2.2a1 1 0 0 1 1-.25 11 11 0 0 0 3.6.6 1 1 0 0 1 1 1V20a1 1 0 0 1-1 1A17 17 0 0 1 3 4a1 1 0 0 1 1-1h3.5a1 1 0 0 1 1 1 11 11 0 0 0 .6 3.6 1 1 0 0 1-.25 1z" fill="var(--lime-text)"/></svg>
        +330 2460-5519
      </li>
      <li class="contact__item">
        <svg class="contact__icon" viewBox="0 0 24 24"><rect x="2" y="5" width="20" height="14" fill="none" stroke="var(--lime-text)" stroke-width="2"/><path d="M2 5 L12 13 L22 5" fill="none" stroke="var(--lime-text)" stroke-width="2"/></svg>
        info@harlowdentalcentre.com
      </li>
      <li class="contact__item">
        <svg class="contact__icon" viewBox="0 0 24 24"><circle cx="12" cy="12" r="10" fill="none" stroke="var(--lime-text)" stroke-width="2"/><path d="M2 12 H22 M12 2 C7 7 7 17 12 22 M12 2 C17 7 17 17 12 22" fill="none" stroke="var(--lime-text)" stroke-width="1.6"/></svg>
        www.harlowdentalcentre.com
      </li>
    </ul>

    <div class="mark">
      <div class="mark__square"></div>
      <p class="mark__name">HARLOW</p>
    </div>
  </div>
</body>
</html>
```